Korrabel Ice Creamery tourist signage

We need to give passing tourists a snapshot of what great fun they can have visiting our brand new Ice creamery located in Timboon, 17km North of the Great Ocean Road and Famous 12 Apostles in Victoria Australia. So the sign needs to be more than directional, need to be enticing. needs to be designed in a manner that project quality. ( keep in mind cars travelling at 80km don't have a lot of time to read too much)
Size is 2.2metres wide by 1.4 meters high
This sign needs to be succinct. Needs to convey fun and a little indulgence but not in a 'tacky' or 'cheap' way.
Needs to offer indulgent imagery of course, our logo too and direction.

Target Market(s)

Tourists, domestic and internationals

Industry/Entity Type

Tourism

Font styles to use
Other font styles liked:
• sacred cow

Colors
add136
fdf3f8
b8a6cd
fabb94
fcca95
85acd3
fbf289

Requirements
Must have
• Convey fun, whimsy indulgence and value ( keeping in mind we need to entice these people a further 17km up the road!)
Nice to have
• White space and clear imagery with
Should not have
• Bold bling colours, be busy looking and cheap looking, needs to convey quality .

```html
<!DOCTYPE html>
<html lang="en">
<head>
<meta charset="utf-8">
<title>Korrabel Ice Creamery – Road Sign</title>
<link rel="stylesheet" href="https://fonts.googleapis.com/css2?family=Lato:wght@900&display=swap">
<style>
  :root {
    --paper: #ffffff;
    --band-dark: #9c1c22;
    --band-light: #b32a30;
    --headline: #ffffff;
    --brand-ink: #1e1e1e;
    --brand-green: #8cc63f;
    --photo-top: #eadbd0;
    --photo-bottom: #dfe9d2;
  }
  html, body {
    margin: 0;
    padding: 0;
    overflow: hidden;
    background: var(--paper);
  }
  .sign {
    position: relative;
    width: 1200px;
    height: 764px;
    background: var(--paper);
    overflow: hidden;
    font-family: "Lato", Arial, sans-serif;
  }
  .sign__band {
    position: absolute;
    left: 0;
    top: 68px;
    width: 1200px;
    height: 360px;
    background: linear-gradient(90deg, var(--band-dark) 0%, var(--band-light) 55%, var(--band-dark) 100%);
  }
  .sign__headline {
    position: absolute;
    left: 560px;
    top: 92px;
    width: 580px;
    margin: 0;
    color: var(--headline);
    font-weight: 900;
    font-size: 142px;
    line-height: 146px;
    letter-spacing: -1px;
    text-align: center;
    white-space: nowrap;
  }
  .sign__photo {
    position: absolute;
    left: 45px;
    top: 0;
    width: 520px;
    height: 764px;
    background: linear-gradient(180deg, var(--photo-top) 0%, var(--photo-bottom) 100%);
  }
  .brand {
    position: absolute;
    left: 625px;
    top: 548px;
    display: flex;
    align-items: center;
    gap: 22px;
  }
  .brand__dot {
    width: 92px;
    height: 92px;
    flex: none;
  }
  .brand__name {
    margin: 0;
    color: var(--brand-ink);
    font-weight: 900;
    font-size: 46px;
    line-height: 52px;
    letter-spacing: 2px;
    text-transform: uppercase;
    white-space: nowrap;
  }
</style>
</head>
<body>
  <main class="sign">
    <div class="sign__band"></div>
    <h1 class="sign__headline">17 KM<br>AHEAD</h1>
    <div class="sign__photo" role="img" aria-label="Photograph of a young child enjoying a strawberry ice cream cone"></div>
    <div class="brand">
      <svg class="brand__dot" viewBox="0 0 92 92" aria-hidden="true">
        <circle cx="46" cy="46" r="46" fill="var(--brand-green)"/>
      </svg>
      <p class="brand__name">Korrabel<br>Ice Creamery</p>
    </div>
  </main>
</body>
</html>
```